Oriel Photography Business Card

I need a business card designed for a photography business based in Perth, Western Australia called Oriel Photography.

We specialise in wedding, event photography and portrait photography.

The business card must borrow the style of the attached logo.

The hex codes for the colours in the logo are:
#ED1D85 - Pink
#89C23E - Green
#37282F - Black

The name on the card will be:
Name: Tobrian
Phone: 0417395268
Website: www.orielphotography.example.com.au
Facebook: orielphotography

I am open and happy to accept creative concepts.

I’d like some space at the back for writing notes and appointment details.

```html
<!DOCTYPE html>
<html lang="en">
<head>
<meta charset="utf-8">
<title>Oriel Photography — Business Card</title>
<link rel="stylesheet" href="https://fonts.googleapis.com/css2?family=Cinzel:wght@400&family=Open+Sans:ital,wght@0,400;0,600;0,700;1,400&family=Raleway:wght@400&display=swap">
<style>
  :root {
    --pink: #ED1D85;
    --green: #89C23E;
    --ink: #37282F;
    --muted: #6b6166;
    --paper: #ffffff;
    --backdrop: #ecebe9;
    --line: #8a8286;
    --social: #9aa0a8;
  }
  * { box-sizing: border-box; margin: 0; padding: 0; }
  html, body { width: 1200px; height: 720px; overflow: hidden; }
  body {
    background: var(--backdrop);
    font-family: "Open Sans", Arial, sans-serif;
    color: var(--ink);
    position: relative;
  }
  .card {
    position: absolute;
    top: 205px;
    width: 540px;
    height: 309px;
    background: var(--paper);
    overflow: hidden;
    box-shadow: 0 2px 8px rgba(0,0,0,0.12);
  }
  .card--front { left: 40px; }
  .card--back { left: 620px; }

  /* Front */
  .brand-mark {
    position: absolute; left: 238px; top: 22px;
    width: 64px; height: 64px; border-radius: 50%;
    background: radial-gradient(circle, var(--green) 0 38%, var(--pink) 40% 100%);
  }
  .brand-name {
    position: absolute; left: 0; right: 0; top: 96px;
    text-align: center; white-space: nowrap;
    font-family: "Raleway", Arial, sans-serif; font-weight: 400;
    font-size: 15px; letter-spacing: 0.62em;
    text-transform: uppercase; color: var(--ink);
    padding-left: 0.62em;
  }
  .person-name {
    position: absolute; left: 0; right: 0; top: 120px;
    text-align: center; font-weight: 700; font-size: 17px;
    color: var(--pink); letter-spacing: 0.03em; text-transform: uppercase;
  }
  .contact-list {
    position: absolute; left: 0; right: 0; top: 150px;
    list-style: none; display: flex; flex-direction: column; align-items: center; gap: 4px;
    font-size: 12.5px; color: var(--ink); white-space: nowrap;
  }
  .contact-list li { display: flex; align-items: center; gap: 6px; }
  .contact-icon { width: 12px; height: 12px; flex: none; }
  .contact-icon--social { background: var(--social); border-radius: 2px; }
  .front-waves { position: absolute; left: 0; bottom: 0; width: 540px; height: 140px; }

  /* Back */
  .back-watermark {
    position: absolute; left: 205px; top: 90px;
    width: 150px; height: 150px; border-radius: 50%;
    background: var(--pink); opacity: 0.08;
  }
  .appointment-title {
    position: absolute; left: 0; right: 0; top: 24px;
    text-align: center; font-family: "Cinzel", Georgia, serif; font-weight: 400;
    font-size: 21px; letter-spacing: 0.06em; color: var(--pink);
  }
  .title-rule {
    position: absolute; left: 90px; right: 90px; top: 60px;
    border-top: 1px solid var(--line);
  }
  .form-row {
    position: absolute; left: 44px; right: 30px;
    display: flex; align-items: flex-end; gap: 8px;
    font-size: 15px; color: var(--muted); white-space: nowrap;
  }
  .form-row > * { flex: none; }
  .form-row--name { top: 84px; }
  .form-row--date { top: 130px; }
  .form-row--next { top: 172px; }
  .form-row--days { top: 216px; }
  .day-label { font-weight: 700; color: var(--ink); }
  .write-line { width: 150px; border-bottom: 1px dotted var(--ink); height: 18px; }
  .write-line--date { width: 158px; }
  .write-box { width: 104px; height: 26px; border: 1px solid var(--line); }
  .write-box--small { width: 30px; height: 24px; margin-right: 10px; }
  .meridiem { font-size: 14px; }
  .spacer { width: 14px; }
  .cancellation-note {
    position: absolute; left: 0; right: 0; top: 266px;
    text-align: center; font-style: italic; font-size: 15px; color: var(--muted);
    white-space: nowrap;
  }
</style>
</head>
<body>

<section class="card card--front" aria-label="Business card front">
  <div class="brand-mark" aria-hidden="true"></div>
  <h1 class="brand-name">Oriel Photography</h1>
  <p class="person-name">Tobrian</p>
  <ul class="contact-list">
    <li>
      <svg class="contact-icon" viewBox="0 0 12 12" aria-hidden="true">
        <circle cx="6" cy="6" r="6" fill="#89C23E"/>
        <path d="M4 3.2c.4 0 .7.9.6 1.2l-.4.4c.3.8.9 1.4 1.7 1.8l.4-.4c.3-.2 1.2.2 1.2.6 0 .6-.6 1-1.1 1C4.8 7.6 3.3 6 3.2 4.3 3.2 3.8 3.5 3.2 4 3.2z" fill="#fff"/>
      </svg>
      0417395268
    </li>
    <li><span class="contact-icon contact-icon--social" aria-hidden="true"></span>orielphotography</li>
    <li>
      <svg class="contact-icon" viewBox="0 0 12 12" aria-hidden="true">
        <circle cx="6" cy="6" r="6" fill="#89C23E"/>
        <circle cx="6" cy="6" r="3" fill="none" stroke="#fff" stroke-width="1"/>
      </svg>
      www.orielphotography.example.com.au
    </li>
  </ul>
  <svg class="front-waves" viewBox="0 0 540 140" preserveAspectRatio="none" aria-hidden="true">
    <path d="M0 140 L0 120 C120 80 260 110 380 70 C450 48 500 30 540 20 L540 140 Z" fill="#89C23E"/>
    <path d="M0 140 L0 124 C130 92 260 122 390 86 C460 66 505 52 540 46 L540 58 C500 66 460 80 395 100 C270 136 140 118 0 140 Z" fill="#ED1D85"/>
    <path d="M0 140 L0 132 C140 110 270 140 400 108 C465 92 505 80 540 72 L540 140 Z" fill="#ffffff"/>
  </svg>
</section>

<section class="card card--back" aria-label="Business card back">
  <div class="back-watermark" aria-hidden="true"></div>
  <h2 class="appointment-title">Your Appointment</h2>
  <div class="title-rule"></div>
  <div class="form-row form-row--name">
    <span>Name :</span><span class="write-line"></span>
    <span class="spacer"></span>
    <span>Time :</span><span class="write-box"></span><span class="meridiem">am / pm</span>
  </div>
  <div class="form-row form-row--date">
    <span>Date :</span><span class="write-line write-line--date"></span>
  </div>
  <div class="form-row form-row--next">
    <span>Next Appointment</span>
    <span class="spacer"></span>
    <span class="day-label">THU</span><span class="write-box write-box--small"></span>
    <span class="day-label">FRI</span><span class="write-box write-box--small"></span>
    <span class="day-label">SAT</span><span class="write-box write-box--small"></span>
  </div>
  <div class="form-row form-row--days">
    <span class="day-label">MON</span><span class="write-box write-box--small"></span>
    <span class="day-label">TUE</span><span class="write-box write-box--small"></span>
    <span class="day-label">WED</span><span class="write-box write-box--small"></span>
  </div>
  <p class="cancellation-note">We appreciate a 24 hr. notice for cancellations</p>
</section>

</body>
</html>
```